Website Design - TallyPorchHelpers.net

PLEASE CHECK WORD DOCUMENT ATTACHED FOR WEBSITE FLOW.

Target Market(s)

REAL ESTATE AGENTS ARE THE TARGET MARKET

Industry/Entity Type

Real Estate

Coding

Coded - Design and coding required

Number of Pages Required

4 page

Colors

Designer to choose colors to be used in the design.

Requirements
Must have
• WE LIKE RED LOGO ATTACHED
Nice to have
• PLEASE CHECK WORD DOCUMENT ATTACHED FOR WEBSITE FLOW.
Should not have

```html
<!DOCTYPE html>
<html lang="en">
<head>
<meta charset="utf-8">
<title>TallyPorch Helpers</title>
<link href="https://fonts.googleapis.com/css2?family=Poppins:wght@400;500;600&display=swap" rel="stylesheet">
<style>
:root{
  --red:#e0001b;
  --black:#0b0b0b;
  --white:#ffffff;
  --grey-band:#e6e6e6;
  --cell:#ffffff;
  --cell-alt:#f2f2f2;
  --line:#d4d4d4;
  --text:#222222;
  --tick:#2ecc1f;
}
*{box-sizing:border-box;margin:0;padding:0}
html,body{width:1200px;height:2719px;overflow:hidden}
body{font-family:'Poppins',sans-serif;color:var(--text);background:var(--white);position:relative}
a{color:inherit;text-decoration:none}

.site-header{height:110px;background:var(--black);position:relative;color:var(--white)}
.brand{position:absolute;left:121px;top:24px;display:flex;align-items:center;gap:10px}
.brand-dot{width:22px;height:22px;background:var(--red)}
.brand-name{font-size:20px;font-weight:600;color:var(--white);line-height:1.1}
.main-nav{position:absolute;left:370px;top:40px;display:flex;gap:38px;font-size:15px;font-weight:500}
.header-phone{position:absolute;left:925px;top:40px;display:flex;align-items:center;gap:10px;font-size:15px;font-weight:500}

.hero{height:599px;position:relative;color:var(--white);text-align:center}
.hero-photo{position:absolute;inset:0;background:radial-gradient(ellipse at 58% 45%,#a88458 0%,#6b4c2f 35%,#3a2a1e 70%,#241a14 100%)}
.hero-photo::after{content:"";position:absolute;inset:0;background:rgba(0,0,0,.35)}
.hero-copy{position:absolute;left:0;right:0;top:200px;font-size:24px;font-weight:600;line-height:34px}
.btn-red{background:var(--red);color:var(--white);font-weight:600;display:inline-flex;align-items:center;justify-content:center}
.hero-cta{position:absolute;left:509px;top:335px;width:156px;height:46px;border-radius:23px;font-size:16px}
.hero-dots{position:absolute;left:570px;top:438px;display:flex;gap:8px;align-items:center}
.hero-dots span{width:10px;height:10px;border-radius:50%;background:var(--white)}
.hero-dots .active{width:18px;height:18px;background:transparent;border:2px solid var(--white);position:relative}
.hero-dots .active::after{content:"";position:absolute;inset:3px;border-radius:50%;background:var(--white)}

.audience{height:270px;text-align:center;padding-top:60px}
.audience h2{font-size:27px;font-weight:500;color:var(--black)}
.audience-options{display:flex;gap:17px;justify-content:center;margin-top:33px}
.audience-options a{width:310px;height:76px;font-size:19px;line-height:24px;text-align:center}

.pricing{height:703px;background:var(--grey-band);padding-top:57px;text-align:center}
.pricing h2{font-size:32px;font-weight:500;color:var(--black)}
.price-table{margin:25px auto 0;width:828px;border:1px solid var(--line);padding:6px;display:grid;grid-template-columns:187px repeat(5,120px);grid-template-rows:98px 134px 89px 90px 48px;gap:6px}
.price-table .cell{background:var(--cell);display:flex;align-items:center;justify-content:center}
.price-table .alt{background:var(--cell-alt)}
.price-table .head-label{font-size:24px;font-weight:500;color:var(--black)}
.price-table .plan{flex-direction:column;font-size:18px;font-weight:500;line-height:30px;color:var(--black)}
.price-table .plan b{font-size:22px;font-weight:600}
.price-table .feature{justify-content:flex-start;text-align:left;font-size:12px;line-height:19px;padding:0 16px}
.price-table .blank{background:transparent}
.price-table .buy{height:40px;align-self:end;font-size:16px}

.perks{height:415px;background:var(--black);color:var(--white);text-align:center;padding-top:40px}
.perks h2{font-size:20px;font-weight:600;line-height:31px}
.perk-list{display:flex;gap:7px;justify-content:center;margin-top:40px}
.perk{width:232px;height:238px;border:2px solid var(--white);padding:20px 8px 0;font-size:14px;line-height:25.5px}
.perk svg{display:block;margin:0 auto 18px}

.newsletter{height:323px;text-align:center;padding-top:48px}
.newsletter h2{font-size:30px;font-weight:600;color:var(--black)}
.newsletter p{font-size:15px;line-height:26px;width:760px;margin:18px auto 0;color:#333}
.subscribe-form{display:flex;width:763px;height:67px;margin:38px auto 0}
.subscribe-form .email{flex:1;border:1px solid var(--line);display:flex;align-items:center;padding-left:38px;font-size:15px;color:#777}
.subscribe-form .btn-red{width:285px;font-size:21px}

.site-footer{height:299px;background:var(--black);color:var(--white);position:relative;font-size:15px}
.contact-item{position:absolute;top:54px;display:flex;gap:16px;line-height:26px}
.footer-nav{position:absolute;top:128px;left:0;right:0;display:flex;justify-content:center;gap:56px;font-size:14px;font-weight:500}
.footer-social{position:absolute;top:195px;left:0;right:0;display:flex;justify-content:center;gap:12px}
.footer-social span{width:12px;height:12px;border-radius:50%;background:var(--white)}
.copyright{position:absolute;top:247px;left:0;right:0;text-align:center;font-size:14px}
</style>
</head>
<body>

<header class="site-header">
  <a class="brand" href="#"><span class="brand-dot"></span><span class="brand-name">TallyPorch<br>Helpers</span></a>
  <nav class="main-nav"><a href="#">How It Works</a><a href="#">Service Area</a><a href="#">Pricing</a><a href="#">About Us</a><a href="#">Faq</a></nav>
  <div class="header-phone">
    <svg width="20" height="20" viewBox="0 0 24 24"><path fill="#e0001b" d="M6.6 10.8a15 15 0 0 0 6.6 6.6l2.2-2.2a1 1 0 0 1 1-.25 11.4 11.4 0 0 0 3.6.57 1 1 0 0 1 1 1V20a1 1 0 0 1-1 1A17 17 0 0 1 3 4a1 1 0 0 1 1-1h3.5a1 1 0 0 1 1 1c0 1.25.2 2.45.57 3.57a1 1 0 0 1-.25 1z"/></svg>
    <span>+1 555 014 2290</span>
  </div>
</header>

<section class="hero">
  <div class="hero-photo" role="img" aria-label="Photo of a real estate agent handing a small model house to a client across a desk"></div>
  <p class="hero-copy">Helping Agents Save Time And Money. We Place Signs And<br>Boost Foot Traffic To Your Open Houses Using Proven<br>Marketing Techniques.</p>
  <a class="btn-red hero-cta" href="#">Contact Us</a>
  <div class="hero-dots"><span class="active"></span><span></span><span></span></div>
</section>

<section class="audience">
  <h2>Choose The Option Below That Best Describes You</h2>
  <div class="audience-options">
    <a class="btn-red" href="#">I'm A Full On Brokerage</a>
    <a class="btn-red" href="#">I'm &nbsp;An Ind.<br>Broker With A Team</a>
    <a class="btn-red" href="#">I Need Sign Placement Asap</a>
  </div>
</section>

<section class="pricing">
  <h2>Pricing</h2>
  <div class="price-table">
    <div class="cell alt head-label">Packages</div>
    <div class="cell alt plan">5 Signs<b>$10</b></div>
    <div class="cell alt plan">10 Signs<b>$99</b></div>
    <div class="cell alt plan">15 Signs<b>$199</b></div>
    <div class="cell alt plan">20 Signs<b>$299</b></div>
    <div class="cell alt plan">25 Signs<b>$399</b></div>

    <div class="cell feature">Place signs strategically in best areas according to where the open house is located</div>
    <div class="cell"><svg width="16" height="14" viewBox="0 0 16 14"><path d="M2 7l4 4 8-9" fill="none" stroke="#2ecc1f" stroke-width="2.5"/></svg></div>
    <div class="cell"><svg width="16" height="14" viewBox="0 0 16 14"><path d="M2 7l4 4 8-9" fill="none" stroke="#2ecc1f" stroke-width="2.5"/></svg></div>
    <div class="cell"><svg width="16" height="14" viewBox="0 0 16 14"><path d="M2 7l4 4 8-9" fill="none" stroke="#2ecc1f" stroke-width="2.5"/></svg></div>
    <div class="cell"><svg width="16" height="14" viewBox="0 0 16 14"><path d="M2 7l4 4 8-9" fill="none" stroke="#2ecc1f" stroke-width="2.5"/></svg></div>
    <div class="cell"><svg width="16" height="14" viewBox="0 0 16 14"><path d="M2 7l4 4 8-9" fill="none" stroke="#2ecc1f" stroke-width="2.5"/></svg></div>

    <div class="cell alt feature">Pick Up the signs after the open house</div>
    <div class="cell alt"><svg width="16" height="14" viewBox="0 0 16 14"><path d="M2 7l4 4 8-9" fill="none" stroke="#2ecc1f" stroke-width="2.5"/></svg></div>
    <div class="cell alt"><svg width="16" height="14" viewBox="0 0 16 14"><path d="M2 7l4 4 8-9" fill="none" stroke="#2ecc1f" stroke-width="2.5"/></svg></div>
    <div class="cell alt"><svg width="16" height="14" viewBox="0 0 16 14"><path d="M2 7l4 4 8-9" fill="none" stroke="#2ecc1f" stroke-width="2.5"/></svg></div>
    <div class="cell alt"><svg width="16" height="14" viewBox="0 0 16 14"><path d="M2 7l4 4 8-9" fill="none" stroke="#2ecc1f" stroke-width="2.5"/></svg></div>
    <div class="cell alt"><svg width="16" height="14" viewBox="0 0 16 14"><path d="M2 7l4 4 8-9" fill="none" stroke="#2ecc1f" stroke-width="2.5"/></svg></div>

    <div class="cell feature">Store custom signs for you if needed</div>
    <div class="cell"><svg width="16" height="14" viewBox="0 0 16 14"><path d="M2 7l4 4 8-9" fill="none" stroke="#2ecc1f" stroke-width="2.5"/></svg></div>
    <div class="cell"><svg width="16" height="14" viewBox="0 0 16 14"><path d="M2 7l4 4 8-9" fill="none" stroke="#2ecc1f" stroke-width="2.5"/></svg></div>
    <div class="cell"><svg width="16" height="14" viewBox="0 0 16 14"><path d="M2 7l4 4 8-9" fill="none" stroke="#2ecc1f" stroke-width="2.5"/></svg></div>
    <div class="cell"><svg width="16" height="14" viewBox="0 0 16 14"><path d="M2 7l4 4 8-9" fill="none" stroke="#2ecc1f" stroke-width="2.5"/></svg></div>
    <div class="cell"><svg width="16" height="14" viewBox="0 0 16 14"><path d="M2 7l4 4 8-9" fill="none" stroke="#2ecc1f" stroke-width="2.5"/></svg></div>

    <div class="cell blank"></div>
    <a class="btn-red buy" href="#">Buy Now</a>
    <a class="btn-red buy" href="#">Buy Now</a>
    <a class="btn-red buy" href="#">Buy Now</a>
    <a class="btn-red buy" href="#">Buy Now</a>
    <a class="btn-red buy" href="#">Buy Now</a>
  </div>
</section>

<section class="perks">
  <h2>Sign Up For A Subscription And Get These Marketing<br>Services For Free</h2>
  <div class="perk-list">
    <div class="perk">
      <svg width="56" height="50" viewBox="0 0 56 50"><path d="M28 3C14 3 4 11 4 22c0 6 3 11 8 14l-3 10 11-7c2.5.6 5 1 8 1 14 0 24-8 24-18S42 3 28 3z" fill="none" stroke="#fff" stroke-width="2.5"/><text x="28" y="27" font-family="Poppins,sans-serif" font-size="12" font-weight="500" fill="#fff" text-anchor="middle">SMS</text></svg>
      Send sms blast to your<br>neighborhood informing<br>them your home is for sale<br>and if they know anyone<br>looking to send them over
    </div>
    <div class="perk">
      <svg width="56" height="50" viewBox="0 0 56 50"><path d="M4 20L28 4l24 16v26H4z M4 20l24 16 24-16" fill="none" stroke="#fff" stroke-width="2.5"/><path d="M14 12h28v14M20 17h16M20 22h16" fill="none" stroke="#fff" stroke-width="2"/></svg>
      Email blast &nbsp;to your<br>neighborhood informing<br>them your home is for sale<br>and if they know anyone<br>looking to send them over
    </div>
    <div class="perk">
      <svg width="56" height="50" viewBox="0 0 56 50"><circle cx="28" cy="25" r="21" fill="none" stroke="#fff" stroke-width="2.5"/></svg>
      Newsfeed ads to people in<br>your open house area
    </div>
    <div class="perk">
      <svg width="56" height="50" viewBox="0 0 56 50"><path d="M12 2h24l10 10v36H12z M36 2v10h10" fill="none" stroke="#fff" stroke-width="2.5"/><rect x="15" y="20" width="28" height="18" fill="#fff"/><text x="29" y="34" font-family="Poppins,sans-serif" font-size="14" font-weight="600" fill="#0b0b0b" text-anchor="middle">VB</text></svg>
      VB blast to your<br>neighborhood informing<br>them your home is for sale<br>and if they know anyone<br>looking to send them over
    </div>
  </div>
</section>

<section class="newsletter">
  <h2>Subscribe Our Newsletter</h2>
  <p>Sed ut perspiciatis unde omnis iste natus error sit voluptatem accusantium doloremque laudantium, totam rem aperiam, eaque ipsa quae ab illo inventore</p>
  <div class="subscribe-form"><div class="email">Enter Your Email</div><a class="btn-red" href="#">Subscribe</a></div>
</section>

<footer class="site-footer">
  <div class="contact-item" style="left:140px">
    <svg width="14" height="20" viewBox="0 0 14 20"><path d="M7 0a7 7 0 0 0-7 7c0 5 7 13 7 13s7-8 7-13a7 7 0 0 0-7-7zm0 9.5A2.5 2.5 0 1 1 7 4.5a2.5 2.5 0 0 1 0 5z" fill="#fff"/></svg>
    <span>#42, 88 Maple Lane,<br>Cedarview, FL 1051</span>
  </div>
  <div class="contact-item" style="left:505px">
    <svg width="18" height="18" viewBox="0 0 24 24"><path fill="#fff" d="M6.6 10.8a15 15 0 0 0 6.6 6.6l2.2-2.2a1 1 0 0 1 1-.25 11.4 11.4 0 0 0 3.6.57 1 1 0 0 1 1 1V20a1 1 0 0 1-1 1A17 17 0 0 1 3 4a1 1 0 0 1 1-1h3.5a1 1 0 0 1 1 1c0 1.25.2 2.45.57 3.57a1 1 0 0 1-.25 1z"/></svg>
    <span>+1 555 014 2290</span>
  </div>
  <div class="contact-item" style="left:775px">
    <svg width="18" height="14" viewBox="0 0 18 14"><rect width="18" height="14" fill="#fff"/><path d="M1 1l8 6 8-6" fill="none" stroke="#0b0b0b" stroke-width="1.6"/></svg>
    <span>info@tallyporchhelpers.net</span>
  </div>
  <nav class="footer-nav"><a href="#">How It Works</a><a href="#">Service Area</a><a href="#">Pricing</a><a href="#">About Us</a><a href="#">Faq</a></nav>
  <div class="footer-social" aria-label="Social links"><span></span><span></span><span></span><span></span></div>
  <p class="copyright">© Copyright 2018 | All Rights Reserved</p>
</footer>

</body>
</html>
```